Business Card Design for Software Development Company

I am looking for a business card design the incorporates my new logo (attached below).

Key information to include:
Name: Martin Quelbrook
Title: CEO
Email: martin@brightwellcivic.example
Phone: 555-218-9403
Website: www.brightwellcivic.example

NOTE: This design should be easy to edit so that we can order cards for different members of our team.

```html
<!DOCTYPE html>
<html lang="en">
<head>
<meta charset="utf-8">
<title>Brightwell Labs — Business Card</title>
<link href="https://fonts.googleapis.com/css2?family=Montserrat:wght@600&family=Poppins:wght@400;700&display=swap" rel="stylesheet">
<style>
  :root {
    --page-bg: #161616;
    --card-top: #2d4456;
    --card-bottom: #354f61;
    --white: #ffffff;
    --teal: #12b09b;
    --orange: #ea7e27;
    --red: #d8452b;
  }
  * { margin: 0; padding: 0; box-sizing: border-box; }
  html, body { width: 900px; height: 1200px; overflow: hidden; }
  body { background: var(--page-bg); position: relative; font-family: 'Poppins', sans-serif; color: var(--white); }

  .card {
    position: absolute;
    left: 135px;
    width: 630px;
    height: 360px;
    background: linear-gradient(120deg, var(--card-top), var(--card-bottom));
  }
  .card--front { top: 213px; }
  .card--back { top: 627px; }

  .wordmark {
    display: flex;
    align-items: center;
    gap: 10px;
    font-family: 'Montserrat', sans-serif;
    font-weight: 600;
    color: var(--white);
    white-space: nowrap;
    letter-spacing: -0.5px;
  }
  .wordmark__dot { background: var(--orange); flex: none; }

  .card--front .wordmark { position: absolute; right: 42px; top: 272px; font-size: 44px; }
  .card--front .wordmark__dot { width: 26px; height: 26px; }

  .card--back .wordmark { position: absolute; left: 40px; top: 164px; font-size: 26px; }
  .card--back .wordmark__dot { width: 16px; height: 16px; }

  .divider { position: absolute; left: 315px; top: 121px; width: 2px; height: 120px; background: var(--white); }

  .contact { position: absolute; left: 334px; top: 118px; }
  .contact__name {
    font-weight: 700;
    font-size: 23px;
    line-height: 1.1;
    background: linear-gradient(180deg, var(--teal) 45%, var(--red) 100%);
    -webkit-background-clip: text;
    background-clip: text;
    color: transparent;
  }
  .contact__title { font-size: 14px; letter-spacing: 0.5px; margin-top: 2px; }
  .contact__rule { width: 30px; height: 2px; margin: 4px 0 10px; background: linear-gradient(90deg, var(--teal), var(--orange)); }
  .contact__list { list-style: none; }
  .contact__item { display: flex; align-items: center; gap: 6px; font-size: 15px; height: 25px; }
  .contact__item--phone { letter-spacing: 3px; }
  .contact__icon { width: 15px; height: 15px; flex: none; }
</style>
</head>
<body>
  <section class="card card--front" aria-label="Card front">
    <div class="wordmark"><span class="wordmark__dot"></span>Brightwell Labs</div>
  </section>

  <section class="card card--back" aria-label="Card back">
    <div class="wordmark"><span class="wordmark__dot"></span>Brightwell Labs</div>
    <div class="divider"></div>
    <div class="contact">
      <h1 class="contact__name">Martin Quelbrook</h1>
      <p class="contact__title">CEO</p>
      <div class="contact__rule"></div>
      <ul class="contact__list">
        <li class="contact__item contact__item--phone">
          <svg class="contact__icon" viewBox="0 0 24 24" aria-hidden="true"><path fill="#d8452b" d="M6.6 10.8a15.1 15.1 0 0 0 6.6 6.6l2.2-2.2a1 1 0 0 1 1-.25 11.4 11.4 0 0 0 3.6.57 1 1 0 0 1 1 1V20a1 1 0 0 1-1 1A17 17 0 0 1 3 4a1 1 0 0 1 1-1h3.5a1 1 0 0 1 1 1c0 1.25.2 2.45.57 3.57a1 1 0 0 1-.25 1z"/></svg>
          555-218-9403
        </li>
        <li class="contact__item">
          <svg class="contact__icon" viewBox="0 0 24 24" aria-hidden="true"><rect x="2" y="5" width="20" height="14" fill="#d8452b"/><path d="M2 5l10 8 10-8" fill="#12b09b"/></svg>
          martin@brightwellcivic.example
        </li>
        <li class="contact__item">
          <svg class="contact__icon" viewBox="0 0 24 24" aria-hidden="true"><circle cx="12" cy="12" r="10" fill="#d8452b"/><path d="M2 12h20M12 2c3 3 3 17 0 20M12 2c-3 3-3 17 0 20" stroke="#12b09b" stroke-width="1.6" fill="none"/></svg>
          www.brightwellcivic.example
        </li>
      </ul>
    </div>
  </section>
</body>
</html>
```